Lotstallmart.com Webpage Design

Design Brief for lotstallmart.com (Copy of Brief also in attached Word file)

Name of Website- lotstallmart.com (existing logo and look & feel of website to be changed)

Logo - Finalised. The logo files are attached with the brief as “logo.jpeg”. The “Blue- Grey” version of the logo is for use on lighter backgrounds and the “Orange-White” version of the logo is for use on darker backgrounds. (A full Black version of the logo is also attached). Both versions may be used in different parts of the website. All attached files are in .png format.
Status - The website in functional and is undergoing user trials. However, we want to improve the look & feel of the website so at it seems
a. cotemporary,
b. Easy to Navigate
c. professional and
d. Vibrant.

Please visit ‘lotstallmart.com’ to check out the website and its functionalities – please use it only as a reference for the features & functions to be provided, however the designer should use a ‘Free Hand’ in designing the composition of various parts of the webpage without getting too influenced by the existing design

Objective of the Website ‘lotstallmart.com –
a. It is a portal focussed on listing of ‘Retail’ specific real-estate properties by developers, owners and realty brokers. The properties shall listed under the following four categories-
i. Retail Malls
ii. Shopping Complexes
iii. High-street shops
iv. Retail Warehouses
*refer lotstallmart.com for better clarity

b. The abovementioned properties shall be listed either for ‘Sale’ or ‘rent\lease’ or both

c. Users shall visit the site in case they wish to acquire a retail \ shop space either on ‘sale’ or ‘rent’. These Users would be able to specify the ‘Search Criteria’ through the tool-bars provided on the website – the ‘Search Criteria’ shall comprise of ‘Type of space category’, ‘City’, ‘Locality’, transaction type ie ‘Rent \ Sale’ and ‘Area Range’

d. The main revenue model for the website shall be listing fee ( or advertising charges ) payable by those listing their properties on the website.

Three Main Pages of Website (lotstallmart.com) that need to be designed -
a. Main Home Page (visit the web link - http://lotstallmart.com/ ) - The main home page has the “Search Toolbar” for specifying of Search Criteria by the User. It shall also have the following features & functions-
i. Main Advertising Banner
ii. Featured Projects
iii. New Launches
iv. Toolbar with buttons – ‘Advertise with Us’, ‘Listings Alert’, ‘Mart Wizards’, ‘Advertiser Login’

b. Property Listings Page (visit the web link - http://lotstallmart.com/gurgaon-in-india ) - The List of property options that match the Criteria specified by the ‘User’ get displayed on this page.

c. Property Detail Page - When the ‘User’ clicks on the “More….” Button on the ‘Property Listings Page’ (given in point b. above) the web page with the details of the property opens. (For Example – visit the web link - http://lotstallmart.com/vorne-Shopping-Complex-vorne-quadrion-gurgaon-636 )

Note:- Please refer to attached ‘Shopping’ related images the designer may use them on the website to provide a look & feel of retail if required – either separately or rotate in a single window

Target Market(s)

Retailers & Investors looking for retail space, Real Estate Brokers, Developers

Industry/Entity Type

Advertising

Number of Pages Required

3 page

Requirements
Must have
• Refer to existing site lotstallmart.com -- all the existing functionalities are a must have.
Nice to have
• The Designer may use the retail related images on the website if required for making it more vibrant. Refer attached images Shopping(1-6).jpg

```html
<!DOCTYPE html>
<html lang="en">
<head>
<meta charset="utf-8">
<title>Lotstallmart.com – Retail Space Portal</title>
<link rel="stylesheet" href="https://fonts.googleapis.com/css2?family=Open+Sans:wght@400;600;700&family=Oxygen:wght@400;700&display=swap">
<style>
:root{
  --blue:#1d9be8;
  --blue-deep:#1486d6;
  --orange:#ff5a00;
  --orange-light:#ff7a1a;
  --ink:#222;
  --text:#444;
  --muted:#888;
  --grey-band:#ececec;
  --topbar:#4d4d4d;
  --footer:#6e6e6e;
  --white:#fff;
  --line:#d4d4d4;
}
*{box-sizing:border-box;margin:0;padding:0}
html,body{width:1200px;height:4027px;overflow:hidden}
body{font-family:"Open Sans",Arial,sans-serif;color:var(--text);background:var(--white);font-size:13px}
.container{width:1020px;margin-left:90px;position:relative}

/* top city bar */
.city-bar{height:27px;background:var(--topbar)}
.city-bar ul{list-style:none;display:flex;gap:6px;height:27px;align-items:center;font-size:10px;font-weight:600;color:#eee}
.city-bar li+li::before{content:"-";margin-right:6px;color:#aaa}

/* header */
.site-header{height:86px}
.brand{position:absolute;left:0;top:22px;display:flex;align-items:center;gap:10px}
.brand-dot{width:34px;height:34px;border-radius:50%;background:var(--blue)}
.brand-name{font-family:"Oxygen",sans-serif;font-weight:700;font-size:30px;color:var(--blue);letter-spacing:-.5px}
.list-cta{position:absolute;right:0;top:14px;font-size:10px;color:#666}
.main-nav{position:absolute;right:0;top:37px;display:flex;align-items:center;gap:12px;font-size:12px;font-weight:600;color:#444}
.main-nav a{color:inherit;text-decoration:none;padding:5px 10px;border-radius:2px}
.main-nav .is-active{background:var(--blue);color:var(--white)}
.main-nav .btn-login{background:var(--orange);color:var(--white);margin-left:14px}
.main-nav .btn-register{background:#555;color:var(--white);margin-left:-6px}

/* hero */
.hero{height:504px;display:flex}
.hero-photo{width:684px;height:504px;position:relative;background:linear-gradient(120deg,#9fb86a 0%,#6f8f4a 35%,#b7b3a3 65%,#8a8f94 100%)}
.hero-caption{position:absolute;left:110px;top:380px;font-family:"Oxygen",sans-serif;font-size:27px;color:var(--white);text-shadow:0 1px 3px rgba(0,0,0,.5)}
.hero-dots{position:absolute;left:413px;top:438px;display:flex;gap:6px}
.hero-dots span{width:9px;height:9px;border-radius:50%;background:rgba(255,255,255,.6)}
.hero-dots span:first-child{background:var(--white)}
.search-panel{width:336px;height:504px;background:linear-gradient(180deg,#26a4ee,#1791df);position:relative;color:var(--white)}
.search-panel h2{position:absolute;left:0;right:0;top:68px;text-align:center;font-family:"Oxygen",sans-serif;font-weight:400;font-size:21px}
.search-panel .format-note{position:absolute;left:0;right:0;top:108px;text-align:center;font-size:10px}
.search-panel .format-note::after{content:"";display:block;width:120px;height:1px;background:rgba(255,255,255,.5);margin:6px auto 0}
.format-options{position:absolute;left:43px;top:150px;width:260px;display:grid;grid-template-columns:142px 118px;row-gap:14px;font-size:10px}
.format-options label{display:flex;align-items:center;gap:6px}
.check{width:13px;height:13px;background:var(--white);border:1px solid #cfe6f7;display:inline-flex;align-items:center;justify-content:center}
.search-field{position:absolute;left:43px;width:252px;height:34px;border:1px solid rgba(255,255,255,.55);background:rgba(255,255,255,.12);font-size:10px;padding:0 10px;display:flex;align-items:center;justify-content:space-between}
.search-field.has-arrow::after{content:"";width:0;height:0;border-left:4px solid transparent;border-right:4px solid transparent;border-top:5px solid var(--white)}
.search-btn{position:absolute;left:43px;top:413px;width:252px;height:44px;background:var(--orange);font-size:13px;font-weight:600;display:flex;align-items:center;justify-content:center;letter-spacing:.3px}

/* about band */
.about{height:269px;background:var(--grey-band)}
.about p{position:absolute;left:50px;top:78px;width:485px;font-size:12.5px;line-height:24px;color:#333}
.about p a{color:#333;text-decoration:underline}
.category{position:absolute;display:flex;align-items:center;gap:14px;font-size:14px;color:#333;line-height:18px}
.category .ring{width:54px;height:54px;border-radius:50%;border:2px solid #555;display:flex;align-items:center;justify-content:center;background:var(--white)}
.cat-malls{left:632px;top:86px}
.cat-complex{left:839px;top:86px}
.cat-highstreet{left:632px;top:178px}
.cat-warehouse{left:839px;top:178px}

/* listing sections */
.listing-section{position:relative}
.section-title{text-align:center;font-family:"Oxygen",sans-serif;font-weight:400;font-size:33px;color:var(--ink)}
.section-sub{display:flex;align-items:center;justify-content:center;gap:10px;font-size:10px;color:#666;margin-top:8px}
.section-sub::before,.section-sub::after{content:"";width:60px;height:1px;background:#999}
.slider-dots{position:absolute;right:0;top:26px;display:flex;gap:4px}
.slider-dots span{width:11px;height:11px;border-radius:50%;border:1px solid var(--blue)}
.slider-dots span:first-child{background:var(--blue)}
.card-grid{display:grid;grid-template-columns:repeat(4,252px);column-gap:4px;row-gap:27px;margin-top:50px}
.project-card{height:322px;background:var(--white);text-align:center;position:relative}
.card-name{height:40px;background:var(--blue);color:var(--white);font-weight:700;font-size:14px;display:flex;align-items:center;justify-content:center}
.card-photo{height:188px;position:relative}
.card-pin{position:absolute;left:50%;bottom:-14px;transform:translateX(-50%)}
.card-location{margin-top:22px;color:var(--blue);font-size:12px;font-weight:600}
.card-type{margin-top:4px;font-size:12.5px;font-weight:700;color:#222}
.card-link{display:block;margin-top:10px;font-size:11px;color:#555;text-decoration:none}
.card-link.is-highlight{color:var(--orange);font-weight:600}
.tone-a{background:linear-gradient(180deg,#b9d4ee,#8fa1ae 60%,#6d6a62)}
.tone-b{background:linear-gradient(180deg,#2b3a66,#6a5b6e 55%,#c08d58)}
.tone-c{background:linear-gradient(180deg,#7fb3e3,#c9a25a 55%,#4b4f3e)}
.tone-d{background:linear-gradient(180deg,#cfe2f4,#9fb3c1 55%,#7d8a78)}
.tone-e{background:linear-gradient(180deg,#e6e6e6,#b6a79a 50%,#4c5d63)}
.tone-f{background:linear-gradient(180deg,#4a6f9e,#9bb3cd 55%,#6e6e6e)}

.featured{height:859px;padding-top:54px}
.launches{height:926px;padding-top:70px}

/* wizards band */
.wizards{height:457px;background:radial-gradient(ellipse at 50% 0%,var(--orange-light) 0%,var(--orange) 55%,#f25200 100%);color:var(--white);text-align:center}
.wizards h2{position:absolute;left:0;right:0;top:76px;font-family:"Oxygen",sans-serif;font-weight:400;font-size:22px}
.wizards p{position:absolute;left:200px;right:200px;top:124px;font-size:12px;line-height:20px}
.wiz-field{position:absolute;height:37px;border:1px solid rgba(255,255,255,.6);font-size:10px;text-align:left;padding:10px 12px;color:#ffe3cf}
.wiz-email{left:251px;top:210px;width:255px}
.wiz-mobile{left:517px;top:210px;width:252px}
.wiz-message{left:251px;top:253px;width:518px;height:80px}
.wiz-send{position:absolute;left:455px;top:344px;width:97px;height:38px;border:1px solid var(--white);font-size:13px;font-weight:600;display:flex;align-items:center;justify-content:center;gap:8px}

/* alert + editor row */
.alert-row{height:529px;display:flex}
.listing-alert{width:510px;height:529px;background:radial-gradient(ellipse at 50% 40%,#3cb2f5,#1a95e4 70%);color:var(--white);text-align:center;position:relative}
.listing-alert h2{position:absolute;left:0;right:0;top:70px;font-family:"Oxygen",sans-serif;font-weight:400;font-size:20px}
.listing-alert .alert-note{position:absolute;left:120px;right:120px;top:116px;font-size:10px;line-height:16px}
.alert-field{position:absolute;left:146px;width:255px;height:35px;border:1px solid rgba(255,255,255,.7);font-size:10px;padding:0 10px;display:flex;align-items:center;justify-content:space-between;text-align:left}
.alert-field.has-arrow::after{content:"";width:0;height:0;border-left:4px solid transparent;border-right:4px solid transparent;border-top:5px solid var(--white)}
.alert-hint{position:absolute;left:146px;font-size:9px;text-align:left}
.alert-subscribe{position:absolute;left:181px;top:411px;width:150px;height:38px;border:1px solid var(--white);font-size:13px;font-weight:600;display:flex;align-items:center;justify-content:center;gap:8px}
.editor-choice{width:510px;height:529px;position:relative;background:linear-gradient(110deg,#2b2b2b 0%,#3d3d3d 45%,#6a6a6a 100%);color:var(--white)}
.editor-choice h2{position:absolute;left:74px;top:170px;font-family:"Oxygen",sans-serif;font-weight:400;font-size:21px}
.editor-choice p{position:absolute;left:74px;top:210px;width:270px;font-size:12px;line-height:18px}
.editor-more{position:absolute;left:74px;top:327px;width:98px;height:34px;border:1px solid var(--white);font-size:12px;font-weight:600;display:flex;align-items:center;justify-content:center;gap:8px}

/* social */
.social{height:196px;position:relative}
.social-link{position:absolute;top:62px;width:80px;height:80px;border-radius:50%;border:3px solid #8a8a8a}

/* footer */
.site-footer{height:174px;background:var(--footer);color:#f0f0f0;font-size:10px}
.footer-links{position:absolute;left:0;top:66px;line-height:24px}
.footer-links span{margin-right:10px}
.copyright{position:absolute;left:796px;top:60px;line-height:16px}
</style>
</head>
<body>

<div class="city-bar">
  <ul class="container">
    <li>Bangalore</li><li>Chennai</li><li>Greater Noida</li><li>Gurgaon</li><li>Hyderabad</li><li>Jaipur</li><li>Khanna</li><li>Kolkatta</li><li>Mumbai</li><li>Noida</li><li>Pune</li><li>Surat</li>
  </ul>
</div>

<header class="site-header container">
  <div class="brand"><span class="brand-dot"></span><span class="brand-name">lotstallmart</span></div>
  <div class="list-cta">List Your Property Here</div>
  <nav class="main-nav">
    <a class="is-active" href="#">Home</a>
    <a href="#">Advertise with Us</a>
    <a href="#">Mart Wizards</a>
    <a href="#">Listing Alert</a>
    <a class="btn-login" href="#">&#9656; Advertiser Login</a>
    <a class="btn-register" href="#">&#9656; New Advertiser - Register</a>
  </nav>
</header>

<section class="hero container">
  <div class="hero-photo" role="img" aria-label="Banner photograph: senior couple shopping together at a retail mall">
    <div class="hero-caption">Shops at Cox Town Bangalore</div>
    <div class="hero-dots"><span></span><span></span><span></span><span></span></div>
  </div>
  <form class="search-panel">
    <h2>Select Retail Format</h2>
    <div class="format-note">Meaning of Retail Format</div>
    <div class="format-options">
      <label><span class="check"><svg width="9" height="9" viewBox="0 0 10 10"><path d="M1 5l3 3 5-6" fill="none" stroke="#1d9be8" stroke-width="2"/></svg></span>Retail Malls</label>
      <label><span class="check"></span>High Street Shops</label>
      <label><span class="check"></span>Shopping Complex</label>
      <label><span class="check"></span>Retail Warehouses</label>
    </div>
    <div class="search-field" style="top:231px">Enter Keywords</div>
    <div class="search-field has-arrow" style="top:276px">Sale Or Rent Or Both</div>
    <div class="search-field has-arrow" style="top:322px">Select City</div>
    <div class="search-field has-arrow" style="top:368px">Select Locality/Micro Market</div>
    <div class="search-btn">SEARCH NOW</div>
  </form>
</section>

<section class="about container">
  <p>The Lotstallmart.com is a Specialised Web based platform for Retail Space, featuring properties across India under various formats such as Retail Malls, Shopping Complexes, High-street Shops. Also featured are Retail Warehouses which provide the logistic back-end for the retail business. Lotstallmart.com is useful to various category of users as follows: a. Devel <a href="#">Learn More &gt;&gt;</a></p>
  <div class="category cat-malls"><span class="ring"><svg width="26" height="26" viewBox="0 0 26 26"><path d="M3 23V9l10-6 10 6v14z" fill="none" stroke="#444" stroke-width="2"/><rect x="10" y="15" width="6" height="8" fill="#444"/></svg></span><span>Retail<br>Malls</span></div>
  <div class="category cat-complex"><span class="ring"><svg width="26" height="26" viewBox="0 0 26 26"><rect x="4" y="5" width="18" height="18" fill="none" stroke="#444" stroke-width="2"/><path d="M8 10h3M15 10h3M8 15h3M15 15h3" stroke="#444" stroke-width="2"/></svg></span><span>Shopping<br>Complexes</span></div>
  <div class="category cat-highstreet"><span class="ring"><svg width="26" height="26" viewBox="0 0 26 26"><path d="M5 9h16l-2 14H7z" fill="none" stroke="#444" stroke-width="2"/><path d="M9 9V6a4 4 0 0 1 8 0v3" fill="none" stroke="#444" stroke-width="2"/></svg></span><span>High-Street<br>Shops</span></div>
  <div class="category cat-warehouse"><span class="ring"><svg width="26" height="26" viewBox="0 0 26 26"><path d="M2 5h4l3 12h12l2-8H8" fill="none" stroke="#444" stroke-width="2"/><circle cx="10" cy="21" r="2" fill="#444"/><circle cx="19" cy="21" r="2" fill="#444"/></svg></span><span>Retail<br>Warehouses</span></div>
</section>

<section class="listing-section featured container">
  <h2 class="section-title">Featured Retail Projects</h2>
  <div class="section-sub">Across India</div>
  <div class="slider-dots" style="top:62px"><span></span><span></span><span></span></div>
  <div class="card-grid">
    <article class="project-card"><div class="card-name">Magnora</div><div class="card-photo tone-d" role="img" aria-label="Photo of a shopping complex building"><svg class="card-pin" width="22" height="30" viewBox="0 0 22 30"><path d="M11 1a10 10 0 0 1 10 10c0 7-10 18-10 18S1 18 1 11A10 10 0 0 1 11 1z" fill="#1d9be8" stroke="#fff" stroke-width="2"/><circle cx="11" cy="11" r="4" fill="#fff"/></svg></div><div class="card-location">Surat - Althan</div><div class="card-type">Shopping Complex</div><a class="card-link is-highlight" href="#">View the Listing &rsaquo;</a></article>
    <article class="project-card"><div class="card-name">Vantra 81 High Street</div><div class="card-photo tone-b" role="img" aria-label="Photo of a high street building lit at dusk"><svg class="card-pin" width="22" height="30" viewBox="0 0 22 30"><path d="M11 1a10 10 0 0 1 10 10c0 7-10 18-10 18S1 18 1 11A10 10 0 0 1 11 1z" fill="#1d9be8" stroke="#fff" stroke-width="2"/><circle cx="11" cy="11" r="4" fill="#fff"/></svg></div><div class="card-location">Faridabad - Sector-81</div><div class="card-type">Shopping Complex</div><a class="card-link" href="#">View the Listing &rsaquo;</a></article>
    <article class="project-card"><div class="card-name">Orvel 24K</div><div class="card-photo tone-c" role="img" aria-label="Photo of a tall retail tower"><svg class="card-pin" width="22" height="30" viewBox="0 0 22 30"><path d="M11 1a10 10 0 0 1 10 10c0 7-10 18-10 18S1 18 1 11A10 10 0 0 1 11 1z" fill="#1d9be8" stroke="#fff" stroke-width="2"/><circle cx="11" cy="11" r="4" fill="#fff"/></svg></div><div class="card-location">Surat - Althan</div><div class="card-type">Shopping Complex</div><a class="card-link" href="#">View the Listing &rsaquo;</a></article>
    <article class="project-card"><div class="card-name">K4K Metropolitan</div><div class="card-photo tone-a" role="img" aria-label="Photo of a modern mall facade"><svg class="card-pin" width="22" height="30" viewBox="0 0 22 30"><path d="M11 1a10 10 0 0 1 10 10c0 7-10 18-10 18S1 18 1 11A10 10 0 0 1 11 1z" fill="#1d9be8" stroke="#fff" stroke-width="2"/><circle cx="11" cy="11" r="4" fill="#fff"/></svg></div><div class="card-location">Gurgaon - Sector-65</div><div class="card-type">Shopping Complex</div><a class="card-link" href="#">View the Listing &rsaquo;</a></article>
    <article class="project-card"><div class="card-name">Zenva Skyline Mall</div><div class="card-photo tone-e" role="img" aria-label="Photo of a mall entrance"><svg class="card-pin" width="22" height="30" viewBox="0 0 22 30"><path d="M11 1a10 10 0 0 1 10 10c0 7-10 18-10 18S1 18 1 11A10 10 0 0 1 11 1z" fill="#1d9be8" stroke="#fff" stroke-width="2"/><circle cx="11" cy="11" r="4" fill="#fff"/></svg></div><div class="card-location">Surat - Althan</div><div class="card-type">Shopping Complex</div><a class="card-link is-highlight" href="#">View the Listing &rsaquo;</a></article>
    <article class="project-card"><div class="card-name">Vantra 81 High Street</div><div class="card-photo tone-f" role="img" aria-label="Photo of a retail building corner"><svg class="card-pin" width="22" height="30" viewBox="0 0 22 30"><path d="M11 1a10 10 0 0 1 10 10c0 7-10 18-10 18S1 18 1 11A10 10 0 0 1 11 1z" fill="#1d9be8" stroke="#fff" stroke-width="2"/><circle cx="11" cy="11" r="4" fill="#fff"/></svg></div><div class="card-location">Faridabad - Sector-81</div><div class="card-type">Shopping Complex</div><a class="card-link" href="#">View the Listing &rsaquo;</a></article>
    <article class="project-card"><div class="card-name">Orvel 24K</div><div class="card-photo tone-c" role="img" aria-label="Photo of a retail tower at street level"><svg class="card-pin" width="22" height="30" viewBox="0 0 22 30"><path d="M11 1a10 10 0 0 1 10 10c0 7-10 18-10 18S1 18 1 11A10 10 0 0 1 11 1z" fill="#1d9be8" stroke="#fff" stroke-width="2"/><circle cx="11" cy="11" r="4" fill="#fff"/></svg></div><div class="card-location">Surat - Althan</div><div class="card-type">Shopping Complex</div><a class="card-link" href="#">View the Listing &rsaquo;</a></article>
    <article class="project-card"><div class="card-name">TRX One Vista Center</div><div class="card-photo tone-a" role="img" aria-label="Photo of a commercial centre with roads"><svg class="card-pin" width="22" height="30" viewBox="0 0 22 30"><path d="M11 1a10 10 0 0 1 10 10c0 7-10 18-10 18S1 18 1 11A10 10 0 0 1 11 1z" fill="#1d9be8" stroke="#fff" stroke-width="2"/><circle cx="11" cy="11" r="4" fill="#fff"/></svg></div><div class="card-location">Gurgaon - Sector-65</div><div class="card-type">Shopping Complex</div><a class="card-link" href="#">View the Listing &rsaquo;</a></article>
  </div>
</section>

<section class="wizards container">
  <h2>Mart Wizards</h2>
  <p>Post your Retail Space requirement with us and our experts shall get back with suitable options and even help you in your transaction. This is a Free Service!</p>
  <div class="wiz-field wiz-email">Enter Email</div>
  <div class="wiz-field wiz-mobile">Mobile</div>
  <div class="wiz-field wiz-message">Message</div>
  <div class="wiz-send">Send <span>&rsaquo;</span></div>
</section>

<section class="listing-section launches container">
  <h2 class="section-title">Featured New Launches</h2>
  <div class="section-sub">Across India</div>
  <div class="slider-dots" style="top:78px"><span></span><span></span><span></span></div>
  <div class="card-grid" style="margin-top:42px">
    <article class="project-card"><div class="card-name">Magnora</div><div class="card-photo tone-e" role="img" aria-label="Photo of a mall atrium interior"><svg class="card-pin" width="22" height="30" viewBox="0 0 22 30"><path d="M11 1a10 10 0 0 1 10 10c0 7-10 18-10 18S1 18 1 11A10 10 0 0 1 11 1z" fill="#1d9be8" stroke="#fff" stroke-width="2"/><circle cx="11" cy="11" r="4" fill="#fff"/></svg></div><div class="card-location">Surat - Althan</div><div class="card-type">Shopping Complex</div><a class="card-link is-highlight" href="#">View the Listing &rsaquo;</a></article>
    <article class="project-card"><div class="card-name">Vantra 81 High Street</div><div class="card-photo tone-b" role="img" aria-label="Photo of a lit shopping street at night"><svg class="card-pin" width="22" height="30" viewBox="0 0 22 30"><path d="M11 1a10 10 0 0 1 10 10c0 7-10 18-10 18S1 18 1 11A10 10 0 0 1 11 1z" fill="#1d9be8" stroke="#fff" stroke-width="2"/><circle cx="11" cy="11" r="4" fill="#fff"/></svg></div><div class="card-location">Faridabad - Sector-81</div><div class="card-type">Shopping Complex</div><a class="card-link" href="#">View the Listing &rsaquo;</a></article>
    <article class="project-card"><div class="card-name">Orvel 24K</div><div class="card-photo tone-f" role="img" aria-label="Photo of a retail plaza under blue sky"><svg class="card-pin" width="22" height="30" viewBox="0 0 22 30"><path d="M11 1a10 10 0 0 1 10 10c0 7-10 18-10 18S1 18 1 11A10 10 0 0 1 11 1z" fill="#1d9be8" stroke="#fff" stroke-width="2"/><circle cx="11" cy="11" r="4" fill="#fff"/></svg></div><div class="card-location">Surat - Althan</div><div class="card-type">Shopping Complex</div><a class="card-link" href="#">View the Listing &rsaquo;</a></article>
    <article class="project-card"><div class="card-name">K4K Metropolitan</div><div class="card-photo tone-d" role="img" aria-label="Photo of a mid-rise retail building"><svg class="card-pin" width="22" height="30" viewBox="0 0 22 30"><path d="M11 1a10 10 0 0 1 10 10c0 7-10 18-10 18S1 18 1 11A10 10 0 0 1 11 1z" fill="#1d9be8" stroke="#fff" stroke-width="2"/><circle cx="11" cy="11" r="4" fill="#fff"/></svg></div><div class="card-location">Gurgaon - Sector-65</div><div class="card-type">Shopping Complex</div><a class="card-link" href="#">View the Listing &rsaquo;</a></article>
    <article class="project-card"><div class="card-name">Zenva Skyline Mall</div><div class="card-photo tone-f" role="img" aria-label="Photo of a glass mall tower"><svg class="card-pin" width="22" height="30" viewBox="0 0 22 30"><path d="M11 1a10 10 0 0 1 10 10c0 7-10 18-10 18S1 18 1 11A10 10 0 0 1 11 1z" fill="#1d9be8" stroke="#fff" stroke-width="2"/><circle cx="11" cy="11" r="4" fill="#fff"/></svg></div><div class="card-location">Surat - Althan</div><div class="card-type">Shopping Complex</div><a class="card-link" href="#">View the Listing &rsaquo;</a></article>
    <article class="project-card"><div class="card-name">Vantra 81 High Street</div><div class="card-photo tone-b" role="img" aria-label="Photo of a retail building at dusk"><svg class="card-pin" width="22" height="30" viewBox="0 0 22 30"><path d="M11 1a10 10 0 0 1 10 10c0 7-10 18-10 18S1 18 1 11A10 10 0 0 1 11 1z" fill="#1d9be8" stroke="#fff" stroke-width="2"/><circle cx="11" cy="11" r="4" fill="#fff"/></svg></div><div class="card-location">Faridabad - Sector-81</div><div class="card-type">Shopping Complex</div><a class="card-link" href="#">View the Listing &rsaquo;</a></article>
    <article class="project-card"><div class="card-name">Orvel 24K</div><div class="card-photo tone-b" role="img" aria-label="Photo of a curved building at night"><svg class="card-pin" width="22" height="30" viewBox="0 0 22 30"><path d="M11 1a10 10 0 0 1 10 10c0 7-10 18-10 18S1 18 1 11A10 10 0 0 1 11 1z" fill="#1d9be8" stroke="#fff" stroke-width="2"/><circle cx="11" cy="11" r="4" fill="#fff"/></svg></div><div class="card-location">Surat - Althan</div><div class="card-type">Shopping Complex</div><a class="card-link" href="#">View the Listing &rsaquo;</a></article>
    <article class="project-card"><div class="card-name">TRX One Vista Center</div><div class="card-photo tone-a" role="img" aria-label="Photo of an office and retail centre"><svg class="card-pin" width="22" height="30" viewBox="0 0 22 30"><path d="M11 1a10 10 0 0 1 10 10c0 7-10 18-10 18S1 18 1 11A10 10 0 0 1 11 1z" fill="#1d9be8" stroke="#fff" stroke-width="2"/><circle cx="11" cy="11" r="4" fill="#fff"/></svg></div><div class="card-location">Gurgaon - Sector-65</div><div class="card-type">Shopping Complex</div><a class="card-link" href="#">View the Listing &rsaquo;</a></article>
  </div>
</section>

<section class="alert-row container">
  <form class="listing-alert">
    <h2>— Listing Alert —</h2>
    <div class="alert-note">Subscribe for Fortnightly Email update on New Listings @ Lotstallmart</div>
    <div class="alert-field" style="top:191px">Enter Email</div>
    <div class="alert-field has-arrow" style="top:242px">Select Question</div>
    <div class="alert-hint" style="top:282px">(select retail format of interest)</div>
    <div class="alert-field has-arrow" style="top:314px">Select City</div>
    <div class="alert-hint" style="top:354px">(select cities of interest)</div>
    <div class="alert-subscribe">Subscribe <span>&rsaquo;</span></div>
  </form>
  <div class="editor-choice" role="img" aria-label="Photograph: shopper holding bags in a dim mall setting">
    <h2>Editor's Choice</h2>
    <p>A "Select" Listing of Retail Properties Handpicked by our Editors based on their own positive evaluation on parameters &amp; attributes such as Design Concept, Location, Developer, Success Potential. So Read On to Check Out for yourself...</p>
    <div class="editor-more">More <span>&rsaquo;</span></div>
  </div>
</section>

<section class="social container" aria-label="Social links">
  <span class="social-link" style="left:321px"></span>
  <span class="social-link" style="left:420px"></span>
  <span class="social-link" style="left:520px"></span>
  <span class="social-link" style="left:622px"></span>
</section>

<footer class="site-footer">
  <div class="container">
    <div class="footer-links">
      <div><span>About Us</span><span>Privacy Policy</span><span>Terms of Use</span><span>Contact Us</span><span>Site Map</span></div>
      <div><span>Retail Malls</span><span>Shopping Complex</span><span>High-Street Shops</span><span>Retail Warehouses</span></div>
    </div>
    <div class="copyright">Copyright © 2015 Bharat Retail Hub.com<br>All rights reserved</div>
  </div>
</footer>

</body>
</html>
```